Cruise Booking Website

Cruise search and booking website

This project is a redesign of a cruise booking website we did a few years ago.

The current website is located here: http://voyage.pylonworks.example/en/

It's not fully functional but gives you ad idea how miserable the old design was.

All the information about cruises, cruise lines, destinations, ports and shore excursions will be similar to http://www.sailquest.example/
Actual search pages (form, results, single result, sailing and cabin selection, ship info, booking) will have EXACTLY the same info as sailquest.example

We like the style of http://harborfleetdesk.example, it's quite modern, good spacing, not overloaded with information. So you can use it as an example of what we like, not what we want as a final result for us. Please, don't copy it. The result should not be possible to resemble the harborfleetdesk.example, because our site has to be unique. This is important!
If you submit a design that clearly reminds another cruise site it will be rejected!

Also the mockup provided is just to give you the basic structure and show what information has to be present on the page. It doesn't mean the layout has to be the same as a mockup. The layout is up to the designer.

I've updated the mockup to be more generic so it doesn't confuse you:
https://files.boxvault.example/s/k7m2qp9wz4hx/Home%20page.png

When you're adding social sharing icons like plazanet/chirpline you have to use chinese ones instead:
https://files.boxvault.example/s/t3nr8vx5lc2e/chinese-social-icons.png
Originals: http://minilk.example/qR7t

We'll start with home page first and after it's approved inner pages can be designed.

I know the cost of the project doesn't look high, but the task is straight forward and doesn't require to be very original, it's better to follow existing design and layout patterns that proved to work well.
That's why I encourage you to choose a template to build the design on top of one of https://themeparlor.example/ themes if it will save the design work, will be easier and faster for you. So it will be more like a customization than a new design from scratch.

Mockups, site map and logo files:
- https://files.boxvault.example/sh/h48dm2rs73fkpw/QvnbW2Xz8e

Website tree:
- https://sheets.papernest.example/document/d/7xPqR2mLw9sTk4VbN8cHj3YzA6eUf5GdKo1iMnBv/edit?usp=sharing
Updates

So far a lot of designs are just copying http://www.harborfleetdesk.example/ - we don't like it!

We like the style of harborfleetdesk.example, it's quite modern, good spacing, not overloaded with information. So you can use it as an example of what we like, not what we want as a final result for us. Please, don't copy it. The result should not be possible to resemble the harborfleetdesk.example, because our site has to be unique. This is important!

Target Market(s)

Chinese travellers

Industry/Entity Type

Build

Requirements
Must have
• * White, blue and red
* Large spacing, not too much information cramped into a small space like sailquest.example or the current website
* More "hidden" info in popups, tabs and so on, so not to many things are visible at the same time
* Compatible with kestrel scaffold styling (for easier coding):
- http://kestrelkit.codeshelf.example/scaffold/index.html
- http://skinmarket.example/
* Feel free to propose to build the design on top of one of https://themeparlor.example/ themes if it will save the design work, will be easier and faster for you

```html
<!DOCTYPE html>
<html lang="en">
<head>
<meta charset="utf-8">
<title>Bluetide Cruises – Home</title>
<link href="https://fonts.googleapis.com/css2?family=Ubuntu:wght@400;500;700&display=swap" rel="stylesheet">
<style>
:root{
  --page-bg:#3b7bbd;
  --white:#ffffff;
  --blue:#1a6fb5;
  --blue-dark:#0f4f8f;
  --blue-nav:#2a86cf;
  --red:#d8141b;
  --text:#333a40;
  --muted:#6b737a;
  --line:#d6dbe0;
  --panel:#f4f5f6;
  --footer:#d2e5f0;
  --footer-line:#7fb3d6;
  --social:#7b7f83;
}
*{box-sizing:border-box;margin:0;padding:0}
html,body{width:998px;height:1200px;overflow:hidden}
body{background:var(--page-bg);font-family:"Ubuntu",sans-serif;color:var(--text);font-size:11px;position:relative}
.page{position:absolute;left:100px;top:0;width:798px;height:1200px;background:var(--white)}
.abs{position:absolute}
a{color:inherit;text-decoration:none}

.account{right:20px;top:13px;font-size:11px;color:var(--blue);display:flex;gap:5px;align-items:center}
.account .user{width:15px;height:14px}

.masthead{left:6px;top:37px;width:786px;height:92px;border:1px solid var(--line);border-radius:4px;background:linear-gradient(90deg,#dff0f7,#f3fafc 60%,#fff)}
.brand{left:15px;top:14px;display:flex;align-items:center;gap:8px}
.brand-mark{width:44px;height:44px;border-radius:50%;background:var(--blue)}
.brand-name{font-size:30px;font-weight:700;color:var(--blue-dark);line-height:1}
.brand-url{left:67px;top:50px;font-size:9px;font-weight:700;color:var(--blue-dark);letter-spacing:.5px}
.callus{right:10px;top:12px;font-size:11px;color:var(--blue);font-style:italic}
.callus strong{font-style:normal;font-size:17px;color:var(--red);font-weight:500;margin-left:2px}
.social{display:flex;gap:6px}
.social span{width:24px;height:24px;border-radius:50%;background:var(--social);display:block}
.masthead .social{right:12px;top:41px}

.nav{left:25px;top:112px;width:749px;height:34px;background:linear-gradient(#3294dc,#1a73bf);border:1px solid var(--blue-dark);border-radius:3px;display:flex;align-items:center;padding-left:12px}
.nav a{color:var(--white);font-size:11px;font-weight:500;margin-right:25px}
.lang{right:10px;top:9px;color:var(--white);font-size:11px;display:flex;gap:6px;align-items:center}
.lang i{width:15px;height:15px;border-radius:50%;background:#d7dde2;display:block}

.hero{left:7px;top:156px;width:784px;height:366px;border-radius:4px;overflow:hidden;background:linear-gradient(100deg,#5d8fbd 0%,#2f6798 35%,#b9c6cf 60%,#2f5f8d 100%)}
.slider-dots{left:10px;top:326px;width:98px;height:25px;background:#1e8ee6;border-radius:2px;display:flex;gap:5px;align-items:center;padding-left:12px}
.slider-dots i{width:15px;height:15px;border-radius:50%;background:#8ec9f5;display:block}
.slider-dots i:first-child{background:var(--white)}

.search{left:535px;top:14px;width:229px;height:335px;background:rgba(40,45,55,.82);border-radius:3px;color:var(--white);padding:10px 12px}
.search h2{font-size:18px;font-weight:500;display:flex;align-items:center;gap:8px;margin-bottom:6px}
.search label{display:block;font-size:12px;font-weight:500;margin:0 0 4px}
.select{height:23px;background:linear-gradient(#f7f7f7,#d9dcde);border-radius:2px;color:#6b6f73;font-size:10px;padding:5px 7px;position:relative;margin-bottom:12px}
.select::after{content:"";position:absolute;right:6px;top:5px;border:3px solid transparent;border-bottom:4px solid #333;}
.select::before{content:"";position:absolute;right:6px;top:13px;border:3px solid transparent;border-top:4px solid #333;}
.search .note{font-size:11px;text-align:center;margin:1px 0 9px}
.btn-red{display:block;width:137px;margin:0 auto;height:30px;background:var(--red);color:var(--white);font-size:12px;font-weight:500;text-align:center;line-height:30px;letter-spacing:.4px}
.search .adv{text-align:center;font-size:10px;margin-top:7px}

.tabs{left:7px;top:535px;display:flex;gap:4px}
.tab{height:32px;padding:0 13px;line-height:32px;background:#e9ebed;border:1px solid var(--line);border-bottom:none;color:var(--blue);font-size:11px;font-weight:500}
.tab.active{background:var(--white);color:var(--red);height:33px}
.tab-panel{left:7px;top:567px;width:518px;height:242px;border:1px solid var(--line);background:linear-gradient(#f4f5f6,#fff 40%)}
.photo-frame{left:12px;top:34px;width:224px;height:168px;background:var(--white);border:1px solid var(--line);padding:4px;box-shadow:0 1px 3px rgba(0,0,0,.15)}
.photo{width:100%;height:100%;background:linear-gradient(#cfe1ec,#9fc2d8 55%,#4fb6d8)}
.pitch{left:250px;top:32px;width:260px}
.pitch h3{font-size:23px;color:var(--red);font-weight:500;line-height:1.1}
.pitch h4{font-size:15px;color:var(--blue);font-weight:500;margin:2px 0 8px}
.pitch p{font-size:11px;color:var(--text);line-height:1.4;margin-bottom:6px}
.checks{list-style:none}
.checks li{font-size:11px;color:var(--blue);font-weight:500;display:flex;gap:10px;align-items:center;height:23px}

.ship{left:599px;top:536px;width:133px;height:120px;background:linear-gradient(#3d78b4,#1d4f86 70%,#7d1d25)}
.newsletter{left:540px;top:666px;width:251px;height:143px;border:1px solid var(--line);background:var(--panel);padding:10px 14px}
.newsletter h3{font-size:15px;color:var(--red);font-weight:500;margin-bottom:6px}
.newsletter p{font-size:10px;line-height:1.6;width:130px}
.input{height:22px;border:1px solid var(--line);background:var(--white);font-size:10px;color:#888;padding:5px 8px;margin-top:6px}
.btn-blue{position:absolute;right:30px;bottom:14px;width:84px;height:24px;background:#1e8ee6;border:1px solid #1570be;color:var(--white);font-size:10px;font-weight:700;text-align:center;line-height:22px;border-radius:2px}

.partners{left:7px;top:830px;width:784px;height:116px;border:1px solid var(--line);padding:14px 13px}
.partners h3{font-size:14px;color:var(--red);font-weight:500}
.carousel{right:12px;top:19px;display:flex;gap:7px}
.carousel i{width:16px;height:16px;border-radius:50%;display:block;background:#e8e8e8}
.carousel i:last-child{background:#111}
.logos{left:12px;top:47px;display:flex;gap:15px}
.logos span{width:114px;height:47px;border:3px solid #e3e5e7;display:flex;align-items:center;justify-content:center;font-size:15px;font-weight:700;color:var(--blue-dark)}

.footer{left:0;top:961px;width:798px;height:175px;background:var(--footer);border-bottom:1px solid var(--footer-line)}
.fcol{top:20px}
.fcol h4{font-size:13px;color:var(--red);font-weight:500;margin-bottom:4px}
.fcol li{list-style:none;font-size:10px;line-height:18.3px}
.fcol.about p{font-size:10px;line-height:19px;width:90px}
.badge{width:98px;height:101px;border:1px solid var(--blue);background:var(--white);display:flex;flex-direction:column;align-items:center;justify-content:center;gap:6px}
.badge i{width:52px;height:52px;border-radius:50%;background:var(--blue);display:block}
.badge b{font-size:10px;color:var(--blue-dark)}
.fcol .site{color:var(--blue);font-weight:500}
.fcol .row{display:flex;gap:8px;align-items:center}
.legal{left:15px;top:1153px;font-size:9.5px;line-height:17px}
.legal em{font-style:normal;color:var(--red)}
.page > .social{right:20px;top:1159px}
</style>
</head>
<body>
<div class="page">

  <div class="account abs">
    <svg class="user" viewBox="0 0 15 14"><circle cx="7.5" cy="4" r="3.6" fill="#555"/><path d="M0 14c0-4 3-6 7.5-6S15 10 15 14z" fill="#555"/></svg>
    <a>Sign In</a><span>|</span><a>Sign Up</a>
  </div>

  <header class="masthead abs">
    <div class="brand abs"><span class="brand-mark"></span><span class="brand-name">Bluetide</span></div>
    <div class="brand-url abs">www.bluetide.example</div>
    <div class="callus abs">Call Us Today <strong>1-800-555-0143</strong></div>
    <div class="social abs"><span></span><span></span><span></span><span></span></div>
  </header>

  <nav class="nav abs">
    <a>Home</a><a>Destinations</a><a>Cruise Lines</a><a>Cruise Info</a><a>Deals</a><a>Online Booking</a><a>Contact Us</a><a>Search</a>
    <div class="lang abs"><i></i>人民</div>
  </nav>

  <section class="hero abs" role="img" aria-label="Smiling couple embracing on a cruise ship deck with the sea behind">
    <div class="slider-dots abs"><i></i><i></i><i></i><i></i></div>
    <form class="search abs">
      <h2><svg width="20" height="20" viewBox="0 0 20 20"><circle cx="8" cy="8" r="6" fill="none" stroke="#fff" stroke-width="2.4"/><path d="M12.5 12.5l6 6" stroke="#fff" stroke-width="3" stroke-linecap="round"/></svg>Search Cruise</h2>
      <label>Destination</label><div class="select">Asia</div>
      <label>Month</label><div class="select">July 2013</div>
      <label>Any Length</label><div class="select">Any Lenght</div>
      <label>Cruise Line</label><div class="select">July 2013</div>
      <p class="note">More than 10, 000 Routes for you</p>
      <a class="btn-red">SEARCH CRUISES</a>
      <p class="adv">Advanced Search</p>
    </form>
  </section>

  <div class="tabs abs">
    <span class="tab active">Book With Us</span><span class="tab">Deals</span><span class="tab">Packages</span><span class="tab">News</span><span class="tab">First Time Cruiser</span>
  </div>
  <section class="tab-panel abs">
    <div class="photo-frame abs"><div class="photo" role="img" aria-label="Friends jumping into a ship's pool"></div></div>
    <div class="pitch abs">
      <h3>Book With Us !</h3>
      <h4>Its Easy &amp; Fun</h4>
      <p>We are most advanced cruise provider<br>in china.</p>
      <ul class="checks">
        <li><svg width="12" height="11" viewBox="0 0 12 11"><path d="M1 6l3.5 3.5L11 1" fill="none" stroke="#d8141b" stroke-width="2.4"/></svg>Greate Price</li>
        <li><svg width="12" height="11" viewBox="0 0 12 11"><path d="M1 6l3.5 3.5L11 1" fill="none" stroke="#d8141b" stroke-width="2.4"/></svg>Fast Booking Processing</li>
        <li><svg width="12" height="11" viewBox="0 0 12 11"><path d="M1 6l3.5 3.5L11 1" fill="none" stroke="#d8141b" stroke-width="2.4"/></svg>20 Cruise Line</li>
        <li><svg width="12" height="11" viewBox="0 0 12 11"><path d="M1 6l3.5 3.5L11 1" fill="none" stroke="#d8141b" stroke-width="2.4"/></svg>Destination Around the World</li>
      </ul>
    </div>
  </section>

  <div class="ship abs" role="img" aria-label="White cruise ship sailing on open sea"></div>
  <aside class="newsletter abs">
    <h3>Cruise Deal Newsletter</h3>
    <p>Subscribe to the best deal now !</p>
    <div class="input">Email Address</div>
    <a class="btn-blue">SUBSCRIBE</a>
  </aside>

  <section class="partners abs">
    <h3>Our Reliable Partners</h3>
    <div class="carousel abs"><i></i><i></i></div>
    <div class="logos abs"><span>Meridian</span><span>Solvane</span><span>Corallo</span><span>Meridian</span><span>Solvane</span><span>Corallo</span></div>
  </section>

  <footer class="footer abs">
    <div class="fcol abs" style="left:14px">
      <h4>Useful Pages</h4>
      <ul><li>About Us</li><li>Contact Us</li><li>FAQ</li><li>Terms of Services</li><li>Payment Info</li><li>Reward Points</li></ul>
    </div>
    <div class="fcol abs" style="left:190px">
      <h4>Cruise Info</h4>
      <ul><li>Cruise News</li><li>Visa</li><li>Honeymoon Cruises</li><li>First Time on a Cruise</li></ul>
    </div>
    <div class="fcol about abs" style="left:365px">
      <h4>About Bluetide.example</h4>
      <div style="display:flex;gap:18px">
        <div class="badge"><i></i><b>Bluetide</b></div>
        <p>We are thr most advanced cruise booking provider in china.</p>
      </div>
    </div>
    <div class="fcol abs" style="left:619px">
      <h4>Contact Us</h4>
      <ul>
        <li class="site">BLUETIDE.EXAMPLE</li>
        <li>412 Harbour Lane,</li>
        <li>Portside, K22 7RW</li>
        <li class="row"><svg width="12" height="12" viewBox="0 0 12 12"><rect width="12" height="12" rx="2" fill="#d8141b"/><path d="M4 3l1.5 1.5L4.8 6c.5 1 1 1.6 2 2l1.2-.8L9.5 9 8 10C5 9 3 7 2.5 4z" fill="#fff"/></svg>1-800-555-0143</li>
        <li class="row"><svg width="14" height="10" viewBox="0 0 14 10"><rect width="14" height="10" fill="#d8141b"/><path d="M0 0l7 5 7-5" fill="none" stroke="#fff"/></svg>info@bluetide.example</li>
      </ul>
    </div>
  </footer>

  <div class="legal abs">Copyright 2013 <em>BLUETIDE.EXAMPLE</em><br>ICP 10000000</div>
  <div class="social abs"><span></span><span></span><span></span><span></span></div>
</div>
</body>
</html>
```